Fun, Clean Business Card For Family Focused Travel Agency

I need a business card using specific colors and fonts as in the uploaded files. Ideally, I would like a large image of the logo on the back and all the contact info on the front. Maybe the stars/dots somewhere in a flowy form.

I do want it the contact information to be clear and easy to read. I don't want it to look too busy. Maybe even a bit minimalist.

I plan or ordering the ROUNDED CORNER business cards from Cardwell Press, so please consider that in your design.

Target Market(s)

Families with children, couples, groups of friends

Contact Information for Business Card

Marla Quint, Owner
Marla@TumbleTrips.example
Cell Phone Number 555-218-4603
Office Phone Number 555-647-1925
Specializing in Glimmerland destinations, Pelican Bay Fun Park, Cruises and All-Inclusive Vacations.

Nice but not required:
www.TumbleTrips.example
Facebook, Instagram, Twitter icons with username: TumbleTrips

Font styles to use
Sans Serif

Requirements
Must have
• Please try to use the colors from the logo as much as possible. I understand lighter shades/colors may be needed for some things.
Should not have
• NO SERIF FONTS. That is really the only thing I do not want at all

```html
<!DOCTYPE html>
<html lang="en">
<head>
<meta charset="utf-8">
<title>Tumble Trips – Business Card</title>
<link href="https://fonts.googleapis.com/css2?family=Exo+2:wght@400;500;600&family=Courgette&display=swap" rel="stylesheet">
<style>
  :root {
    --navy: #0b0f26;
    --white: #ffffff;
    --teal: #16b49a;
    --orange: #f07f2a;
    --sky: #2ea6dc;
    --sun: #d8b82a;
    --ink: #1d2133;
    --backdrop: #e4e6ea;
    --rule: rgba(255,255,255,0.28);
  }
  * { box-sizing: border-box; margin: 0; padding: 0; }
  html, body { width: 1200px; height: 782px; overflow: hidden; }
  body {
    background: var(--backdrop);
    font-family: "Exo 2", sans-serif;
    position: relative;
  }
  .card {
    position: absolute;
    top: 236px;
    width: 540px;
    height: 309px;
    border-radius: 16px;
    overflow: hidden;
    box-shadow: 0 6px 18px rgba(0,0,0,0.18);
  }
  /* Front: contact side */
  .card--front { left: 40px; background: var(--white); }
  .front__band {
    position: absolute; left: 0; right: 0; top: 150px; bottom: 0;
    background: var(--navy);
  }
  .front__art {
    position: absolute; left: 24px; top: 26px;
    width: 200px; height: 250px;
    border-radius: 46% 46% 40% 40%;
    background: linear-gradient(160deg, var(--navy) 0%, #1f2d52 35%, var(--sky) 60%, var(--teal) 80%, var(--orange) 100%);
  }
  .front__name {
    position: absolute; right: 30px; top: 88px;
    font-family: "Courgette", cursive;
    font-size: 31px; color: var(--teal);
    text-align: right;
  }
  .front__title {
    position: absolute; right: 32px; top: 128px;
    font-size: 14px; color: var(--ink); letter-spacing: 0.3px;
  }
  .contact {
    position: absolute; right: 22px; top: 172px;
    list-style: none;
  }
  .contact__item {
    display: flex; justify-content: flex-end; align-items: center;
    gap: 8px;
    height: 27px;
    font-size: 17px; color: var(--white); letter-spacing: 0.2px;
  }
  .contact__icon { width: 16px; height: 16px; flex: none; }
  /* Back: brand side */
  .card--back {
    left: 620px; background: var(--navy);
    display: flex; flex-direction: column; align-items: center; justify-content: center;
  }
  .brand {
    display: flex; align-items: center; gap: 14px;
    margin-bottom: 26px;
  }
  .brand__dot {
    width: 22px; height: 22px; border-radius: 50%;
    background: var(--teal);
  }
  .brand__name {
    font-size: 52px; font-weight: 600; color: var(--white);
    letter-spacing: 0.5px;
  }
  .tagline {
    width: 440px;
    border-top: 1px solid var(--rule);
    border-bottom: 1px solid var(--rule);
    padding: 10px 0;
    text-align: center;
    font-size: 14px; line-height: 1.35; color: var(--white);
  }
</style>
</head>
<body>

  <section class="card card--front" aria-label="Business card front">
    <div class="front__band"></div>
    <div class="front__art" role="img" aria-label="Colourful sailing ship illustration with stars and dots"></div>
    <p class="front__name">Marla Quint</p>
    <p class="front__title">Owner</p>
    <ul class="contact">
      <li class="contact__item">555-218-4603
        <svg class="contact__icon" viewBox="0 0 16 16" aria-hidden="true"><path fill="var(--teal)" d="M3.6 1.5 6 4.2 4.8 5.9c.8 1.9 2.3 3.4 4.2 4.2l1.7-1.2 2.7 2.4-1.4 2.2C6.8 13.4 2.6 9.2 1.4 4.1z"/></svg>
      </li>
      <li class="contact__item">555-647-1925
        <svg class="contact__icon" viewBox="0 0 16 16" aria-hidden="true"><rect x="4" y="1" width="8" height="14" rx="1.5" fill="none" stroke="var(--teal)" stroke-width="1.6"/><circle cx="8" cy="12.3" r="0.9" fill="var(--teal)"/></svg>
      </li>
      <li class="contact__item">Marla@TumbleTrips.example
        <svg class="contact__icon" viewBox="0 0 16 16" aria-hidden="true"><rect x="1" y="3.5" width="14" height="9" rx="1" fill="var(--teal)"/><path d="M1.5 4 8 9l6.5-5" fill="none" stroke="var(--navy)" stroke-width="1.2"/></svg>
      </li>
      <li class="contact__item">www.TumbleTrips.example
        <svg class="contact__icon" viewBox="0 0 16 16" aria-hidden="true"><circle cx="8" cy="8" r="6.5" fill="var(--teal)"/><path d="M1.5 8h13M8 1.5c-2.4 2.6-2.4 10.4 0 13M8 1.5c2.4 2.6 2.4 10.4 0 13" fill="none" stroke="var(--navy)" stroke-width="1"/></svg>
      </li>
    </ul>
  </section>

  <section class="card card--back" aria-label="Business card back">
    <div class="brand">
      <span class="brand__dot"></span>
      <span class="brand__name">Tumble Trips</span>
    </div>
    <p class="tagline">Specializing in Glimmerland destinations, Pelican Bay Fun Park<br>Cruises and All-Inclusive Vacations</p>
  </section>

</body>
</html>
```